Business Cards Design for the electrical wholesaler: clean bold dynamic :)

We need a business card design that would follow our latest brand guidelines. As an electrical wholesaler we want to bring a fresh look and feel into the industry. The design should be clean bold and dynamic. It should come alive with the renewed energy of our green colour. Our grey colour should keep things balanced and complement the notion of maturity and responsibility. We employ Lato as a corporate font however are not bound by this font and we’re open to interpretation here.

Target Market(s)

Electrical contractors

Industry/Entity Type

Business

Contact Information for Business Card

Logo
Name & Surname: Halyna Dorosh
Job Title: Director of Marketing
Email: halya.dorosh@quillmail.example
Cell phone: XXX.XXX.XXXX
Address: 20517 - 87 Ave. Edmonton, AB, Canada. T6K 4N8
Business Phone: 780.555.0184
Website: www.brovix.example

Font styles to use
Other font styles liked:
• Lato

Requirements
Must have
• Logo & website
Nice to have
• Brand elements - some of them you may find in the attached Brand Guidelines (e.g. three lines on the background signifying "W")

```html
<!DOCTYPE html>
<html lang="en">
<head>
<meta charset="utf-8">
<title>Brovix Business Cards</title>
<link rel="stylesheet" href="https://fonts.googleapis.com/css2?family=Work+Sans:wght@400;500;600&display=swap">
<style>
  :root {
    --brand-green: #7cc334;
    --brand-green-light: #86cb3f;
    --brand-grey: #3b3736;
    --ink-white: #ffffff;
    --ink-soft: rgba(255,255,255,0.92);
  }
  * { margin: 0; padding: 0; box-sizing: border-box; }
  html, body {
    width: 1200px; height: 715px; overflow: hidden;
    background: var(--brand-grey);
    font-family: "Work Sans", Arial, sans-serif;
  }
  .canvas {
    position: relative; width: 1200px; height: 715px;
    display: flex; align-items: center; justify-content: center; gap: 40px;
  }
  .card {
    position: relative; width: 540px; height: 309px;
    background: linear-gradient(135deg, var(--brand-green-light), var(--brand-green));
    border-radius: 4px;
    box-shadow: 0 10px 26px rgba(0,0,0,0.35);
    color: var(--ink-white);
    overflow: hidden;
  }
  /* front */
  .card-front .wordmark {
    position: absolute; left: 50%; top: 50%; transform: translate(-50%, -50%);
    display: flex; flex-direction: column; align-items: flex-end;
  }
  .wordmark-row { display: flex; align-items: center; gap: 14px; }
  .wordmark-mark { width: 40px; height: 40px; background: var(--ink-white); border-radius: 4px; }
  .wordmark-name { font-size: 74px; font-weight: 500; line-height: 1; letter-spacing: -1px; }
  .wordmark-tagline { font-size: 11px; font-weight: 500; letter-spacing: 2.4px; margin-top: 4px; }
  /* back */
  .card-back .wordmark {
    position: absolute; left: 34px; top: 112px;
    display: flex; flex-direction: column; align-items: flex-end;
  }
  .card-back .wordmark-mark { width: 26px; height: 26px; border-radius: 3px; }
  .card-back .wordmark-row { gap: 9px; }
  .card-back .wordmark-name { font-size: 46px; }
  .card-back .wordmark-tagline { font-size: 7px; letter-spacing: 1.6px; margin-top: 3px; }
  .divider {
    position: absolute; left: 266px; top: 80px; width: 1px; height: 150px;
    background: var(--ink-soft);
  }
  .contact { position: absolute; left: 286px; top: 84px; }
  .contact-name { font-size: 20px; font-weight: 600; line-height: 1.1; }
  .contact-title { font-size: 12px; font-weight: 400; margin-bottom: 10px; }
  .contact-line { font-size: 12px; line-height: 17px; display: flex; align-items: center; gap: 7px; color: var(--ink-soft); white-space: nowrap; }
  .contact-line svg { width: 9px; height: 9px; flex: none; }
</style>
</head>
<body>
<main class="canvas">
  <section class="card card-front">
    <div class="wordmark">
      <div class="wordmark-row">
        <span class="wordmark-mark"></span>
        <span class="wordmark-name">brovix</span>
      </div>
      <span class="wordmark-tagline">ELECTRICAL WHOLESALERS</span>
    </div>
  </section>

  <section class="card card-back">
    <div class="wordmark">
      <div class="wordmark-row">
        <span class="wordmark-mark"></span>
        <span class="wordmark-name">brovix</span>
      </div>
      <span class="wordmark-tagline">ELECTRICAL WHOLESALERS</span>
    </div>
    <div class="divider"></div>
    <div class="contact">
      <p class="contact-name">Halyna Dorosh</p>
      <p class="contact-title">Director of Marketing</p>
      <p class="contact-line">20517 87ave</p>
      <p class="contact-line">T6K4N8 Edmonton, Alberta</p>
      <p class="contact-line">
        <svg viewBox="0 0 10 10" aria-hidden="true"><path d="M2 1 L4 1 L4.6 3 L3.4 3.8 Q4.4 5.8 6.2 6.6 L7 5.4 L9 6 L9 8 Q5 9 1.8 5 Q1 3 2 1 Z" fill="#fff"/></svg>
        780.555.0184
      </p>
      <p class="contact-line">
        <svg viewBox="0 0 10 10" aria-hidden="true"><rect x="3" y="0.8" width="4" height="8.4" rx="0.8" fill="none" stroke="#fff" stroke-width="1"/><circle cx="5" cy="7.6" r="0.5" fill="#fff"/></svg>
        780.555.0147
      </p>
      <p class="contact-line">
        <svg viewBox="0 0 10 10" aria-hidden="true"><rect x="1" y="2.2" width="8" height="5.6" fill="none" stroke="#fff" stroke-width="1"/><path d="M1 2.4 L5 5.4 L9 2.4" fill="none" stroke="#fff" stroke-width="1"/></svg>
        halya.dorosh@quillmail.example
      </p>
      <p class="contact-line">
        <svg viewBox="0 0 10 10" aria-hidden="true"><circle cx="5" cy="5" r="4" fill="none" stroke="#fff" stroke-width="1"/><path d="M1 5 H9 M5 1 Q2.5 5 5 9 M5 1 Q7.5 5 5 9" fill="none" stroke="#fff" stroke-width="0.8"/></svg>
        www.brovix.example
      </p>
    </div>
  </section>
</main>
</body>
</html>
```